Design a Job Application & CV

I need a design for upcoming job applications that includes a cv. It needs to look as elegant and modern as possible as the application will be send mainly to large corporations and strategy consultancies. I have attached an application that I like for your consideration. One of the more difficult requirements is that it needs to be editable in ms office word for mac/windows.
As stated only the design is part of this project. I will fill in my content later on.
Reason: Dear Designers,
I am going to increase the budget as well as extending the deadline. I am hoping that you can improve upon the design that I have provided in the brief. If you have questions please let me know.
Dear Designers,
Target Market(s)
Human Resources Managers, Senior Consultants and Executives of larger firms
Industry/Entity Type
Office
Requirements
Must have
- 4 Pages including( a cover page, a coverletter page, 2 pages cv)
It should be easy to edit and should be readable by word for mac, i.e. in the *.docx format.
Here is an example of what I like:
http://www.torvenmald.example/applicationexample.pdf
http://www.torvenmald.example/applicationExample.docx
colors that I like are blue, grey, black, white
Nice to have
- icons to indicate sections
Should not have
- invasive cliparts

```html
<!DOCTYPE html>
<html lang="en">
<head>
<meta charset="utf-8">
<title>Application Cover</title>
<link rel="stylesheet" href="https://fonts.googleapis.com/css2?family=Tenor+Sans&display=swap">
<style>
  :root {
    --charcoal-dark: #3b3b3d;
    --charcoal-light: #6b6c6e;
    --accent-blue: #09a6df;
    --paper: #f2f2f4;
    --ink: #58585a;
    --ink-soft: #8a8a8c;
    --white: #ffffff;
  }
  * { margin: 0; padding: 0; box-sizing: border-box; }
  html, body { width: 848px; height: 1200px; overflow: hidden; background: var(--paper); }
  body { font-family: "Tenor Sans", "Optima", sans-serif; }
  .cover { position: relative; width: 848px; height: 1200px; background: var(--paper); }
  .band { position: absolute; left: 0; width: 100%; }
  .band--dark { background: linear-gradient(90deg, var(--charcoal-dark), var(--charcoal-light)); }
  .band--blue { background: var(--accent-blue); }
  .header { top: 0; height: 405px; }
  .position-bar { top: 405px; height: 147px; }
  .header-foot { top: 552px; height: 42px; }
  .footer-blue { top: 1121px; height: 32px; }
  .footer-dark { top: 1153px; height: 47px; }
  .cover-title {
    position: absolute; left: 40px; top: 252px;
    font-size: 84px; font-weight: 400; color: var(--white);
    letter-spacing: -1px; line-height: 1;
  }
  .dotted-rule { position: absolute; left: 0; width: 100%; height: 2px; }
  .dotted-rule--top { top: 439px; }
  .dotted-rule--bottom { top: 510px; }
  .position-title {
    position: absolute; left: 42px; top: 454px;
    font-size: 38px; color: var(--white); line-height: 1;
  }
  .applicant { position: absolute; left: 40px; top: 856px; }
  .applicant-name { font-size: 32px; font-weight: 400; color: var(--ink); line-height: 1; margin-bottom: 18px; }
  .applicant-name .surname { color: var(--accent-blue); }
  .contact { list-style: none; font-size: 18px; color: var(--ink-soft); line-height: 29px; }
</style>
</head>
<body>
<main class="cover">
  <div class="band band--dark header"></div>
  <h1 class="cover-title">APPLICATION</h1>

  <div class="band band--blue position-bar"></div>
  <svg class="dotted-rule dotted-rule--top" width="848" height="2" aria-hidden="true">
    <line x1="0" y1="1" x2="848" y2="1" stroke="#ffffff" stroke-width="1.5" stroke-dasharray="2 3"/>
  </svg>
  <p class="position-title">Job Position Here</p>
  <svg class="dotted-rule dotted-rule--bottom" width="848" height="2" aria-hidden="true">
    <line x1="0" y1="1" x2="848" y2="1" stroke="#ffffff" stroke-width="1.5" stroke-dasharray="2 3"/>
  </svg>

  <div class="band band--dark header-foot"></div>

  <section class="applicant">
    <h2 class="applicant-name">MARELA <span class="surname">OSTVIK</span></h2>
    <ul class="contact">
      <li>2208 Larkfield Avenue, Apt.# 12</li>
      <li>Brennport, CA 90000, USA</li>
      <li>Mobil: : +1 (000) 555 0142</li>
      <li>E-Mail: : marela@mailbox.example</li>
    </ul>
  </section>

  <div class="band band--blue footer-blue"></div>
  <div class="band band--dark footer-dark"></div>
</main>
</body>
</html>
```